Local Mortgage Broker requires DL Flyer

I Require DL sized design for local mortgage broker. Content that will go on the flyer is attached along with the logo.
Looking for a bright & catchy design with that little OOMPH.....on the creative side.
Am looking for a responsive campaign with this style of marketing. The main message is that "We may be able to save thousands of dollars for you, just give us a chance to review your mortgages"

Target Market(s)

All home owners with a mortgage or eople looking to buy their first home.

Industry/Entity Type

Marketing

```html
<!DOCTYPE html>
<html lang="en">
<head>
<meta charset="UTF-8">
<title>Find the Right Finance Solution – DL Flyer</title>
<link rel="stylesheet" href="https://fonts.googleapis.com/css2?family=Roboto+Condensed:wght@700;800&family=PT+Sans:wght@400;700&display=swap">
<style>
  :root {
    --yellow: #fde600;
    --navy: #2b2663;
    --white: #ffffff;
    --photo-light: #ece3dc;
    --photo-warm: #d9b59c;
    --photo-red: #c8553a;
  }
  * { margin: 0; padding: 0; box-sizing: border-box; }
  html, body { width: 1200px; height: 2544px; overflow: hidden; background: var(--navy); }
  .flyer { position: relative; width: 1200px; height: 2544px; background: var(--navy); overflow: hidden; }

  .headline-band {
    position: absolute; left: 0; top: 0; width: 1200px; height: 352px;
    background: var(--yellow);
    display: flex; align-items: center; justify-content: center;
  }
  .headline {
    font-family: "Roboto Condensed", sans-serif; font-weight: 800;
    font-size: 126px; line-height: 1.02; color: var(--navy);
    text-align: center; letter-spacing: 1px;
  }

  .hero-photo {
    position: absolute; left: 0; top: 352px; width: 1200px; height: 840px;
    background:
      radial-gradient(ellipse 380px 280px at 560px 420px, var(--photo-red) 0%, rgba(200,85,58,0) 70%),
      radial-gradient(ellipse 520px 380px at 600px 600px, var(--photo-warm) 0%, rgba(217,181,156,0) 75%),
      linear-gradient(180deg, var(--photo-light) 0%, #d8cfc8 100%);
  }

  .tagline-box {
    position: absolute; left: 48px; top: 912px; width: 400px; height: 160px;
    background: var(--yellow);
    display: flex; align-items: center; justify-content: center;
    font-family: "PT Sans", sans-serif; font-weight: 700;
    font-size: 34px; line-height: 1.2; color: var(--navy); text-align: center;
  }

  .logo-panel { position: absolute; left: 660px; top: 912px; width: 540px; height: 280px; }
  .logo-panel svg { position: absolute; left: 0; top: 0; }
  .logo-name {
    position: absolute; left: 0; width: 540px; top: 176px; text-align: center;
    font-family: "PT Sans", sans-serif; font-weight: 700; font-size: 58px; line-height: 1; color: var(--navy);
  }

  .body {
    position: absolute; left: 56px; top: 1240px; width: 1080px;
    font-family: "PT Sans", sans-serif; color: var(--white);
  }
  .intro { font-size: 37px; line-height: 48px; }
  .services { list-style: none; margin-top: 60px; }
  .services li {
    position: relative; padding-left: 34px;
    font-weight: 700; font-size: 37px; line-height: 50px; color: var(--yellow);
  }
  .services li::before {
    content: ""; position: absolute; left: 0; top: 21px;
    width: 11px; height: 11px; border-radius: 50%; background: var(--yellow);
  }
  .savings { font-size: 37px; line-height: 48px; margin-top: 56px; }

  .call-to-action {
    position: absolute; left: 0; top: 2060px; width: 1200px; text-align: center;
    font-family: "Roboto Condensed", sans-serif; font-weight: 700;
    font-size: 96px; line-height: 116px; color: var(--yellow);
  }

  .web-band {
    position: absolute; left: 0; top: 2340px; width: 1200px; height: 100px;
    background: var(--yellow);
    display: flex; align-items: center; justify-content: center;
    font-family: "PT Sans", sans-serif; font-weight: 700; font-size: 56px; color: var(--navy);
  }
</style>
</head>
<body>
<div class="flyer">
  <header class="headline-band">
    <h1 class="headline">FIND THE RIGHT<br>FINANCE SOLUTION</h1>
  </header>

  <div class="hero-photo" role="img" aria-label="Photo of hands holding a small model house with a red roof"></div>

  <div class="tagline-box">The right loan to<br>suit your individual<br>requirements.</div>

  <div class="logo-panel">
    <svg width="540" height="280" viewBox="0 0 540 280">
      <polygon points="0,280 0,110 270,0 540,110 540,280" fill="#ffffff"/>
    </svg>
    <div class="logo-name">NestPath Finance</div>
  </div>

  <section class="body">
    <p class="intro">Whether you are looking to buy your first home, renovate, refinance or invest, we're here to negotiate the right finance for you. We're a one-stop shop with hundreds of loan options available from across Australia's leading lenders and we'll work with you to find the right finance solution to meet your needs.</p>
    <ul class="services">
      <li>Refinance existing Mortgage</li>
      <li>Purchase First Home</li>
      <li>Purchase Investment Property</li>
      <li>Upgrade or Renovate existing Property</li>
    </ul>
    <p class="savings">We are confident that we may be able to save you thousands of dollars over the term of your loan by simply reviewing your existing home loan.</p>
  </section>

  <p class="call-to-action">Call us on 0412 555 019<br>To find out how!</p>

  <footer class="web-band">www.nestpathfinance.com.au</footer>
</div>
</body>
</html>
```